Redesign Craft Brewing Recipe Website

Originally built with Bootstrap just to get the site going, I am seeking a complete redesign of the sites home page and recipe page. I am an experienced web developer with no graphic background, initially just looking for psd mocks.

I prefer styles that are clean and modern, and would prefer anything that is fun, engaging, and has an organic feel to it. I currently have a cartoon rabbit as a logo, but it needs some modification/tweaking, so any help in that area would be great as well.

Current site:
http://velvetfinch.cloudpagehost.net/

Current launch page/logo:
http://www.velvetfinch.com/

I like the overall layout of the elements currently, but the design sucks.

The launch page is at the following URL

Reason: Still looking for a more modern design. Designs received so far are too similar to the original.

My site is content based and does not contain images or products. Your design should not consist of large images.

Reason: The website has very little images, so the designs need to be more text and content based. The header needs to be very small and should not contain an ad rotater.

Target Market(s)

Home brewers, Craft brewers, Microbreweries, Brewpubs

Requirements
Must have
• Web 2.0 Look and Feel, Fun, Hip, Focus on content
Should not have
• A large photo as a header

```html
<!DOCTYPE html>
<html lang="en">
<head>
<meta charset="utf-8">
<title>Velvetfinch – Craft Beer Recipes</title>
<link href="https://fonts.googleapis.com/css2?family=Montserrat:ital,wght@0,400;0,600;0,700;1,600&family=Oswald:wght@500&display=swap" rel="stylesheet">
<style>
:root{
  --bar-dark:#4e0a08;
  --red-hi:#d41c12;
  --red-lo:#7e0a06;
  --wood-dark:#1e1e1e;
  --wood:#4a4a4a;
  --wood-lite:#5a5a5a;
  --card:#ffffff;
  --card-band:#ececec;
  --stats:#e4e4e4;
  --text:#4a4a4a;
  --muted:#8a8a8a;
  --link:#c0825a;
  --extract:#c8200e;
  --partial:#e08a00;
  --allgrain:#1ca6da;
  --srm-red:#b83a1c;
  --srm-teal:#2a8f80;
  --srm-green:#5a9e12;
  --srm-blue:#1b7cc0;
  --logo-orange:#e8761a;
  --cream:#efe6dc;
  --copy:#a0623a;
}
*{box-sizing:border-box;margin:0;padding:0}
html,body{width:814px;height:1200px;overflow:hidden}
body{position:relative;font-family:"Montserrat",Arial,sans-serif;color:var(--text);background:var(--wood)}
.topbar{position:absolute;left:0;top:0;width:814px;height:19px;background:var(--bar-dark)}
.search{position:absolute;left:95px;top:2px;width:137px;height:15px;background:#fff;border:1px solid #999;font-size:8px;color:#888;padding:2px 4px;white-space:nowrap}
.search-btn{position:absolute;right:0;top:-1px;width:17px;height:15px;border-left:1px solid #999;background:#f2f2f2}
.topnav{position:absolute;right:95px;top:4px;display:flex;gap:20px;font-size:9px;color:#fff;white-space:nowrap}
.header{position:absolute;left:0;top:19px;width:814px;height:123px;background:radial-gradient(ellipse at 50% 20%,var(--red-hi),var(--red-lo) 80%)}
.brand{position:absolute;left:0;top:60px;width:814px;display:flex;justify-content:center;align-items:center;gap:10px}
.brand-dot{width:26px;height:26px;border-radius:50%;background:var(--cream)}
.brand-name{font-family:"Oswald",sans-serif;font-weight:500;font-size:40px;color:var(--logo-orange);letter-spacing:1px;white-space:nowrap}
.tagline-band{position:absolute;left:0;top:142px;width:814px;height:29px;background:linear-gradient(#3a3a3a,#262626)}
.tagline{position:absolute;left:236px;top:8px;font-size:10px;color:#fff;white-space:nowrap;letter-spacing:-.1px}
.share{position:absolute;top:7px;height:12px;background:#eef1f7;border:1px solid #b9c4d8;border-radius:2px}
.social-sq{position:absolute;top:7px;width:13px;height:13px;background:#fff;border-radius:2px}
.filterbar{position:absolute;left:0;top:171px;width:814px;height:41px;background:var(--wood-dark)}
.dropdown{position:absolute;top:7px;height:23px;background:#3b3b3b;border-radius:2px;font-size:9.5px;color:#fff;padding:6px 20px 6px 9px;white-space:nowrap}
.dropdown::after{content:"";position:absolute;right:8px;top:10px;border:4px solid transparent;border-top-color:#bbb}
.dropdown .dim{color:#999}
.main{position:absolute;left:0;top:212px;width:814px;height:900px;background:repeating-linear-gradient(90deg,var(--wood) 0 7px,var(--wood-lite) 7px 9px,#444 9px 16px)}
.grid{position:absolute;left:97px;top:15px;display:grid;grid-template-columns:repeat(4,145px);grid-auto-rows:199px;column-gap:13px;row-gap:11px}
.card{position:relative;background:var(--card);box-shadow:0 1px 3px rgba(0,0,0,.5)}
.photo{position:absolute;left:7px;top:6px;width:131px;height:78px}
.photo-title{position:absolute;left:0;bottom:0;width:100%;height:20px;background:rgba(40,30,20,.72);color:#fff;font-size:8.5px;text-align:center;line-height:20px;white-space:nowrap}
.meta-band{position:absolute;left:7px;top:88px;width:131px;height:30px;background:var(--card-band)}
.counts{position:absolute;left:4px;top:5px;display:flex;gap:5px}
.count{width:17px;text-align:center;font-size:7.5px;color:var(--muted)}
.count svg{display:block;margin:0 auto 2px;width:10px;height:10px;fill:#b5b5b5}
.tag{position:absolute;right:-9px;top:2px;height:11px;padding:0 5px 0 12px;font-size:7.5px;color:#fff;line-height:11px;white-space:nowrap;clip-path:polygon(0 0,100% 0,100% 100%,0 100%,6px 50%)}
.extract{background:var(--extract)}.partial{background:var(--partial)}.allgrain{background:var(--allgrain)}
.style{position:absolute;right:3px;top:15px;font-size:7.5px;color:var(--muted);white-space:nowrap}
.desc{position:absolute;left:9px;top:124px;width:130px;font-size:8px;line-height:12px;color:#444}
.creator{position:absolute;left:9px;top:151px;font-size:7.5px;color:var(--muted);white-space:nowrap}
.creator span{color:var(--link)}
.stats{position:absolute;left:0;top:170px;width:145px;height:29px;background:var(--stats);display:flex}
.stat{width:29px;text-align:center;font-size:7.5px;line-height:10px;padding-top:4px;color:#555}
.stat.srm{color:#fff}
.srm-red{background:var(--srm-red)}.srm-teal{background:var(--srm-teal)}.srm-green{background:var(--srm-green)}.srm-blue{background:var(--srm-blue)}
.footer-band{position:absolute;left:0;top:1112px;width:814px;height:20px;background:#222}
.footer-brand{position:absolute;left:0;top:1092px;width:814px;display:flex;justify-content:center;align-items:center;gap:7px}
.footer-brand .brand-name{font-size:22px}
.footer-brand .brand-dot{width:16px;height:16px}
.beer-art{position:absolute;left:615px;top:1062px;width:97px;height:72px;border-radius:6px;background:linear-gradient(#f0c070,#b8641c)}
.newsletter-wrap{position:absolute;left:0;top:1132px;width:814px;height:68px;background:var(--cream)}
.newsletter{position:absolute;left:100px;top:6px;width:612px;height:34px;background:#fff;border:1px solid #ddd}
.newsletter > *{position:absolute;white-space:nowrap}
.nl-title{left:6px;top:6px;font-family:"Oswald",sans-serif;font-weight:500;font-size:15px;line-height:20px;color:#b22a10}
.nl-copy{left:149px;top:12px;font-size:7px;letter-spacing:-.15px;color:#444}
.nl-input{left:336px;top:7px;width:118px;height:18px;border:1px solid #ccc;border-radius:9px;font-size:7.5px;color:#777;padding:4px 9px}
.nl-join{position:absolute;right:-10px;top:-2px;width:26px;height:20px;border-radius:10px;background:var(--logo-orange);color:#fff;font-size:7px;font-weight:700;text-align:center;line-height:20px}
.nl-connect{left:473px;top:12px;font-size:7.5px;font-style:italic;font-weight:600;color:#333;letter-spacing:-.2px}
.nl-sq{top:9px;width:15px;height:15px;border-radius:2px}
.copyright{position:absolute;left:0;top:48px;width:814px;text-align:center;font-size:8px;color:var(--copy);white-space:nowrap}
</style>
</head>
<body>
<svg width="0" height="0" style="position:absolute">
  <symbol id="i-heart" viewBox="0 0 10 10"><path d="M5 9 1 5C-.5 3 1 .5 3 1c1 .2 1.6 1 2 1.6C5.4 2 6 1.2 7 1c2-.5 3.5 2 2 4Z"/></symbol>
  <symbol id="i-chat" viewBox="0 0 10 10"><path d="M0 1h7v5H3L1 8V6H0Z"/><path d="M8 3h2v5H9v2L7 8H4V7h4Z"/></symbol>
  <symbol id="i-star" viewBox="0 0 10 10"><path d="M5 0l1.5 3.3 3.5.4-2.6 2.4.7 3.5L5 7.8 1.9 9.6l.7-3.5L0 3.7l3.5-.4Z"/></symbol>
</svg>

<div class="topbar">
  <div class="search">Search<span class="search-btn"></span></div>
  <nav class="topnav"><span>Recipes</span><span>About ▾</span><span>Login</span></nav>
</div>

<header class="header">
  <div class="brand"><span class="brand-dot"></span><span class="brand-name">VELVETFINCH</span></div>
</header>

<div class="tagline-band">
  <p class="tagline">Velvetfinch is the easiest way to create and share craft beer recipes.</p>
  <span class="share" style="left:593px;width:46px"></span>
  <span class="share" style="left:642px;width:30px"></span>
  <span class="social-sq" style="left:684px"></span>
  <span class="social-sq" style="left:703px"></span>
</div>

<div class="filterbar">
  <div class="dropdown" style="left:95px;width:85px">Brewing</div>
  <div class="dropdown" style="left:187px;width:86px">Styles</div>
  <div class="dropdown" style="left:280px;width:85px">Match Maker</div>
  <div class="dropdown" style="left:611px;width:107px"><span class="dim">Sort by ›</span> Trending</div>
</div>

<main class="main">
  <div class="grid">
    <!-- row 1 -->
    <article class="card"><div class="photo" role="img" aria-label="Beer being poured into a glass" style="background:linear-gradient(135deg,#e8d890,#8a7a30)"><div class="photo-title">Oak Bastard Sweet Mead</div></div><div class="meta-band"><div class="counts"><div class="count"><svg><use href="#i-heart"/></svg>10</div><div class="count"><svg><use href="#i-chat"/></svg>7</div><div class="count"><svg><use href="#i-star"/></svg>0</div></div><span class="tag extract">Extract</span><span class="style">Belgian Tripel</span></div><p class="desc">Lorem ipsum dolor sit amet, consectetur adipisicing elit.</p><p class="creator">Created by <span>Dana Whitlow</span></p><div class="stats"><div class="stat">2.24%<br>ABV</div><div class="stat">24<br>IBU</div><div class="stat">1.006<br>FG</div><div class="stat">1.022<br>OG</div><div class="stat srm srm-red">4<br>SRM</div></div></article>
    <article class="card"><div class="photo" role="img" aria-label="Oak barrel in a cellar" style="background:linear-gradient(135deg,#5a4a3a,#1a1410)"><div class="photo-title">Oak Bastard Sweet Mead</div></div><div class="meta-band"><div class="counts"><div class="count"><svg><use href="#i-heart"/></svg>8</div><div class="count"><svg><use href="#i-chat"/></svg>15</div><div class="count"><svg><use href="#i-star"/></svg>0</div></div><span class="tag partial">PartialMash</span><span class="style">Mild</span></div><p class="desc">Lorem ipsum dolor sit amet, consectetur adipisicing elit.</p><p class="creator">Created by <span>Dana Whitlow</span></p><div class="stats"><div class="stat">2.24%<br>ABV</div><div class="stat">24<br>IBU</div><div class="stat">1.006<br>FG</div><div class="stat">1.022<br>OG</div><div class="stat srm srm-teal">4<br>SRM</div></div></article>
    <article class="card"><div class="photo" role="img" aria-label="Pints of amber beer on a bar" style="background:linear-gradient(135deg,#c8701c,#3a1a08)"><div class="photo-title">Oak Bastard Sweet Mead</div></div><div class="meta-band"><div class="counts"><div class="count"><svg><use href="#i-heart"/></svg>6</div><div class="count"><svg><use href="#i-chat"/></svg>3</div><div class="count"><svg><use href="#i-star"/></svg>0</div></div><span class="tag allgrain">AllGrain</span><span class="style">Belgian Tripel</span></div><p class="desc">Lorem ipsum dolor sit amet, consectetur adipisicing elit.</p><p class="creator">Created by <span>Dana Whitlow</span></p><div class="stats"><div class="stat">2.24%<br>ABV</div><div class="stat">24<br>IBU</div><div class="stat">1.006<br>FG</div><div class="stat">1.022<br>OG</div><div class="stat srm srm-green">4<br>SRM</div></div></article>
    <article class="card"><div class="photo" role="img" aria-label="Foamy glass of beer" style="background:linear-gradient(#f0e4d0,#b86a20)"><div class="photo-title">Oak Bastard Sweet Mead</div></div><div class="meta-band"><div class="counts"><div class="count"><svg><use href="#i-heart"/></svg>2</div><div class="count"><svg><use href="#i-chat"/></svg>9</div><div class="count"><svg><use href="#i-star"/></svg>0</div></div><span class="tag extract">Extract</span><span class="style">Belgian Tripel</span></div><p class="desc">Lorem ipsum dolor sit amet, consectetur adipisicing elit.</p><p class="creator">Created by <span>Dana Whitlow</span></p><div class="stats"><div class="stat">2.24%<br>ABV</div><div class="stat">24<br>IBU</div><div class="stat">1.006<br>FG</div><div class="stat">1.022<br>OG</div><div class="stat srm srm-red">4<br>SRM</div></div></article>
    <!-- row 2 -->
    <article class="card"><div class="photo" role="img" aria-label="Beer glasses beside a keg" style="background:linear-gradient(135deg,#f4f0ea,#a0642a)"><div class="photo-title">Oak Bastard Sweet Mead</div></div><div class="meta-band"><div class="counts"><div class="count"><svg><use href="#i-heart"/></svg>5</div><div class="count"><svg><use href="#i-chat"/></svg>20</div><div class="count"><svg><use href="#i-star"/></svg>0</div></div><span class="tag allgrain">AllGrain</span><span class="style">Belgian Tripel</span></div><p class="desc">Lorem ipsum dolor sit amet, consectetur adipisicing elit.</p><p class="creator">Created by <span>Dana Whitlow</span></p><div class="stats"><div class="stat">2.24%<br>ABV</div><div class="stat">24<br>IBU</div><div class="stat">1.006<br>FG</div><div class="stat">1.022<br>OG</div><div class="stat srm srm-blue">4<br>SRM</div></div></article>
    <article class="card"><div class="photo" role="img" aria-label="Two glasses of red ale" style="background:linear-gradient(135deg,#d07a1c,#4a1808)"><div class="photo-title">Oak Bastard Sweet Mead</div></div><div class="meta-band"><div class="counts"><div class="count"><svg><use href="#i-heart"/></svg>0</div><div class="count"><svg><use href="#i-chat"/></svg>6</div><div class="count"><svg><use href="#i-star"/></svg>0</div></div><span class="tag extract">Extract</span><span class="style">Munich Helles</span></div><p class="desc">Lorem ipsum dolor sit amet, consectetur adipisicing elit.</p><p class="creator">Created by <span>Dana Whitlow</span></p><div class="stats"><div class="stat">2.24%<br>ABV</div><div class="stat">24<br>IBU</div><div class="stat">1.006<br>FG</div><div class="stat">1.022<br>OG</div><div class="stat srm srm-red">4<br>SRM</div></div></article>
    <article class="card"><div class="photo" role="img" aria-label="Beer tap pouring" style="background:linear-gradient(135deg,#c8c870,#4a5a18)"><div class="photo-title">Oak Bastard Sweet Mead</div></div><div class="meta-band"><div class="counts"><div class="count"><svg><use href="#i-heart"/></svg>3</div><div class="count"><svg><use href="#i-chat"/></svg>8</div><div class="count"><svg><use href="#i-star"/></svg>0</div></div><span class="tag partial">PartialMash</span><span class="style">Mild</span></div><p class="desc">Lorem ipsum dolor sit amet, consectetur adipisicing elit.</p><p class="creator">Created by <span>Dana Whitlow</span></p><div class="stats"><div class="stat">2.24%<br>ABV</div><div class="stat">24<br>IBU</div><div class="stat">1.006<br>FG</div><div class="stat">1.022<br>OG</div><div class="stat srm srm-teal">4<br>SRM</div></div></article>
    <article class="card"><div class="photo" role="img" aria-label="Mugs of beer with hops" style="background:linear-gradient(135deg,#e8dcc0,#8a5a24)"><div class="photo-title">Oak Bastard Sweet Mead</div></div><div class="meta-band"><div class="counts"><div class="count"><svg><use href="#i-heart"/></svg>2</div><div class="count"><svg><use href="#i-chat"/></svg>10</div><div class="count"><svg><use href="#i-star"/></svg>0</div></div><span class="tag allgrain">AllGrain</span><span class="style">Belgian Tripel</span></div><p class="desc">Lorem ipsum dolor sit amet, consectetur adipisicing elit.</p><p class="creator">Created by <span>Dana Whitlow</span></p><div class="stats"><div class="stat">2.24%<br>ABV</div><div class="stat">24<br>IBU</div><div class="stat">1.006<br>FG</div><div class="stat">1.022<br>OG</div><div class="stat srm srm-green">4<br>SRM</div></div></article>
    <!-- row 3 -->
    <article class="card"><div class="photo" role="img" aria-label="Close view of a foamy beer" style="background:linear-gradient(#f2ece0,#b06a1c)"><div class="photo-title">Oak Bastard Sweet Mead</div></div><div class="meta-band"><div class="counts"><div class="count"><svg><use href="#i-heart"/></svg>6</div><div class="count"><svg><use href="#i-chat"/></svg>9</div><div class="count"><svg><use href="#i-star"/></svg>0</div></div><span class="tag partial">PartialMash</span><span class="style">Mild</span></div><p class="desc">Lorem ipsum dolor sit amet, consectetur adipisicing elit.</p><p class="creator">Created by <span>Dana Whitlow</span></p><div class="stats"><div class="stat">2.24%<br>ABV</div><div class="stat">24<br>IBU</div><div class="stat">1.006<br>FG</div><div class="stat">1.022<br>OG</div><div class="stat srm srm-teal">4<br>SRM</div></div></article>
    <article class="card"><div class="photo" role="img" aria-label="Chilled glass of lager" style="background:linear-gradient(135deg,#3a2a18,#d8942a)"><div class="photo-title">Oak Bastard Sweet Mead</div></div><div class="meta-band"><div class="counts"><div class="count"><svg><use href="#i-heart"/></svg>5</div><div class="count"><svg><use href="#i-chat"/></svg>7</div><div class="count"><svg><use href="#i-star"/></svg>0</div></div><span class="tag allgrain">AllGrain</span><span class="style">English Cider</span></div><p class="desc">Lorem ipsum dolor sit amet, consectetur adipisicing elit.</p><p class="creator">Created by <span>Dana Whitlow</span></p><div class="stats"><div class="stat">2.24%<br>ABV</div><div class="stat">24<br>IBU</div><div class="stat">1.006<br>FG</div><div class="stat">1.022<br>OG</div><div class="stat srm srm-blue">4<br>SRM</div></div></article>
    <article class="card"><div class="photo" role="img" aria-label="Pints of amber beer on a bar" style="background:linear-gradient(135deg,#d0781c,#3a1808)"><div class="photo-title">Oak Bastard Sweet Mead</div></div><div class="meta-band"><div class="counts"><div class="count"><svg><use href="#i-heart"/></svg>4</div><div class="count"><svg><use href="#i-chat"/></svg>3</div><div class="count"><svg><use href="#i-star"/></svg>0</div></div><span class="tag extract">Extract</span><span class="style">Belgian Tripel</span></div><p class="desc">Lorem ipsum dolor sit amet, consectetur adipisicing elit.</p><p class="creator">Created by <span>Dana Whitlow</span></p><div class="stats"><div class="stat">2.24%<br>ABV</div><div class="stat">24<br>IBU</div><div class="stat">1.006<br>FG</div><div class="stat">1.022<br>OG</div><div class="stat srm srm-green">4<br>SRM</div></div></article>
    <article class="card"><div class="photo" role="img" aria-label="Pints of beer at a pub counter" style="background:linear-gradient(135deg,#c06a1a,#2a1a10)"><div class="photo-title">Oak Bastard Sweet Mead</div></div><div class="meta-band"><div class="counts"><div class="count"><svg><use href="#i-heart"/></svg>3</div><div class="count"><svg><use href="#i-chat"/></svg>11</div><div class="count"><svg><use href="#i-star"/></svg>0</div></div><span class="tag extract">Extract</span><span class="style">Belgian Tripel</span></div><p class="desc">Lorem ipsum dolor sit amet, consectetur adipisicing elit.</p><p class="creator">Created by <span>Dana Whitlow</span></p><div class="stats"><div class="stat">2.24%<br>ABV</div><div class="stat">24<br>IBU</div><div class="stat">1.006<br>FG</div><div class="stat">1.022<br>OG</div><div class="stat srm srm-red">4<br>SRM</div></div></article>
    <!-- row 4 -->
    <article class="card"><div class="photo" role="img" aria-label="Colourful cocktails and beers" style="background:linear-gradient(135deg,#9ac8e8,#d09a2a)"><div class="photo-title">Oak Bastard Sweet Mead</div></div><div class="meta-band"><div class="counts"><div class="count"><svg><use href="#i-heart"/></svg>8</div><div class="count"><svg><use href="#i-chat"/></svg>14</div><div class="count"><svg><use href="#i-star"/></svg>0</div></div><span class="tag extract">Extract</span><span class="style">Mild</span></div><p class="desc">Lorem ipsum dolor sit amet, consectetur adipisicing elit.</p><p class="creator">Created by <span>Dana Whitlow</span></p><div class="stats"><div class="stat">2.24%<br>ABV</div><div class="stat">24<br>IBU</div><div class="stat">1.006<br>FG</div><div class="stat">1.022<br>OG</div><div class="stat srm srm-teal">4<br>SRM</div></div></article>
    <article class="card"><div class="photo" role="img" aria-label="Beer poured into a glass" style="background:linear-gradient(135deg,#f0d8b0,#b4521a)"><div class="photo-title">Oak Bastard Sweet Mead</div></div><div class="meta-band"><div class="counts"><div class="count"><svg><use href="#i-heart"/></svg>7</div><div class="count"><svg><use href="#i-chat"/></svg>50</div><div class="count"><svg><use href="#i-star"/></svg>0</div></div><span class="tag extract">Extract</span><span class="style">Belgian Tripel</span></div><p class="desc">Lorem ipsum dolor sit amet, consectetur adipisicing elit.</p><p class="creator">Created by <span>Dana Whitlow</span></p><div class="stats"><div class="stat">2.24%<br>ABV</div><div class="stat">24<br>IBU</div><div class="stat">1.006<br>FG</div><div class="stat">1.022<br>OG</div><div class="stat srm srm-green">4<br>SRM</div></div></article>
    <article class="card"><div class="photo" role="img" aria-label="Beer glasses beside a keg" style="background:linear-gradient(135deg,#f4f0ea,#a86a2a)"><div class="photo-title">Oak Bastard Sweet Mead</div></div><div class="meta-band"><div class="counts"><div class="count"><svg><use href="#i-heart"/></svg>4</div><div class="count"><svg><use href="#i-chat"/></svg>20</div><div class="count"><svg><use href="#i-star"/></svg>0</div></div><span class="tag allgrain">AllGrain</span><span class="style">English Cider</span></div><p class="desc">Lorem ipsum dolor sit amet, consectetur adipisicing elit.</p><p class="creator">Created by <span>Dana Whitlow</span></p><div class="stats"><div class="stat">2.24%<br>ABV</div><div class="stat">24<br>IBU</div><div class="stat">1.006<br>FG</div><div class="stat">1.022<br>OG</div><div class="stat srm srm-blue">4<br>SRM</div></div></article>
    <article class="card"><div class="photo" role="img" aria-label="Blurred pint of beer in a pub" style="background:linear-gradient(135deg,#8a5a2a,#3a2214)"><div class="photo-title">Oak Bastard Sweet Mead</div></div><div class="meta-band"><div class="counts"><div class="count"><svg><use href="#i-heart"/></svg>2</div><div class="count"><svg><use href="#i-chat"/></svg>8</div><div class="count"><svg><use href="#i-star"/></svg>0</div></div><span class="tag partial">PartialMash</span><span class="style">Belgian Tripel</span></div><p class="desc">Lorem ipsum dolor sit amet, consectetur adipisicing elit.</p><p class="creator">Created by <span>Dana Whitlow</span></p><div class="stats"><div class="stat">2.24%<br>ABV</div><div class="stat">24<br>IBU</div><div class="stat">1.006<br>FG</div><div class="stat">1.022<br>OG</div><div class="stat srm srm-red">4<br>SRM</div></div></article>
  </div>
</main>

<div class="footer-band"></div>
<div class="footer-brand"><span class="brand-dot"></span><span class="brand-name">VELVETFINCH</span></div>
<div class="beer-art" role="img" aria-label="Group of beer mugs with hops"></div>

<footer class="newsletter-wrap">
  <div class="newsletter">
    <span class="nl-title">JOIN OUR MAILING LIST</span>
    <span class="nl-copy">Sign up for our e-mail list to receive updates</span>
    <span class="nl-input">Your e-mail address<span class="nl-join">JOIN</span></span>
    <span class="nl-connect">Connect with us on</span>
    <span class="nl-sq" style="left:549px;background:#4fb3e0"></span>
    <span class="nl-sq" style="left:568px;background:#3b5a98"></span>
    <span class="nl-sq" style="left:587px;background:#1f77b0"></span>
  </div>
  <p class="copyright">Copyright © 2013 Velvetfinch. All rights reserved.</p>
</footer>
</body>
</html>
```